Brightfield Ventures Inc. Letterhead

Creation of attractive and eye catching letterhead for a business start-up for the construction industry. Letterhead must relate to construction, but avoid standard hammer and tools in the design.

I forgot to add some details, sorry about that. Some pertinent info: Ph: 916-555-0187 brightfieldventures.example 448 Willowmere Ave, Ste 210 Folsom, CA 95999 info@brightfieldventures.example not sure if slogan should be in there" “Connecting construction professionals to create a purpose driven industry.” must be able to be used in word. Thanks!

```html
<!DOCTYPE html>
<html lang="en">
<head>
<meta charset="utf-8">
<title>Brightfield Ventures Inc. Letterhead</title>
<link href="https://fonts.googleapis.com/css2?family=Open+Sans:wght@400;600&family=Lato:wght@400&family=Montserrat:wght@600&display=swap" rel="stylesheet">
<style>
  :root {
    --navy: #0f1a4f;
    --red: #b80d12;
    --ink: #4d4d4d;
    --ink-dark: #333333;
    --paper: #ffffff;
    --backdrop: #e9e9e9;
  }
  * { margin: 0; padding: 0; box-sizing: border-box; }
  html, body {
    width: 1040px; height: 1200px; overflow: hidden;
    background: var(--backdrop);
  }
  .letterhead {
    position: absolute; left: 54px; top: 0;
    width: 931px; height: 1200px;
    background: var(--paper);
    font-family: "Open Sans", sans-serif;
    color: var(--ink);
    overflow: hidden;
  }
  .brand {
    position: absolute; right: 90px; top: 96px;
    display: flex; align-items: center; gap: 10px;
  }
  .brand-mark { width: 16px; height: 16px; background: var(--red); }
  .brand-name {
    font-family: "Montserrat", sans-serif; font-weight: 600;
    font-size: 20px; letter-spacing: 2px; color: var(--navy);
  }
  .block { position: absolute; left: 87px; width: 753px; font-size: 14.6px; }
  .issue-date { top: 215px; }
  .recipient { top: 252px; line-height: 18px; font-style: normal; }
  .salutation { top: 356px; }
  .body-copy { top: 406px; line-height: 27px; text-align: justify; hyphens: auto; }
  .body-copy p + p { margin-top: 27px; }
  .closing { top: 814px; }
  .signatory { top: 890px; }
  .signatory-name { font-size: 19px; font-weight: 600; color: var(--ink-dark); }
  .signatory-title { margin-top: 4px; font-size: 14.6px; }

  .footer-band {
    position: absolute; left: 0; bottom: 0; width: 931px; height: 110px;
    background: var(--navy);
  }
  .footer-rule {
    position: absolute; left: 0; bottom: 118px; width: 931px; height: 6px;
    background: var(--red);
  }
  .footer-address, .footer-contacts {
    position: absolute; font-family: "Lato", sans-serif; font-size: 15px; color: #fff;
  }
  .footer-address { left: 90px; bottom: 34px; }
  .footer-contacts { right: 90px; bottom: 28px; text-align: right; line-height: 20px; list-style: none; }
  .footer-contacts li { display: flex; justify-content: flex-end; align-items: center; gap: 8px; }
  .footer-contacts svg { width: 11px; height: 11px; fill: #fff; }
</style>
</head>
<body>
<main class="letterhead">
  <header class="brand">
    <span class="brand-mark"></span>
    <span class="brand-name">BRIGHTFIELD VENTURES</span>
  </header>

  <p class="block issue-date">Issuing Date: May 5, 2018</p>
  <address class="block recipient">
    Name Of Employee Mr. XYZABC<br>Address of Employee<br>Address Line 2 etc..
  </address>
  <p class="block salutation">Dear Mr.XYZABC</p>

  <div class="block body-copy">
    <p>Lorem Ipsum has been the industry's standard dummy text ever since the 1500s, when an unknown printer took a galley of type and scrambled it to make a type specimen book. It has survived not only five centuries, but also the leap into electronic typesetting, remaining essentially unchanged. It was popularised in the 1960s with the release of Marlowe Press sheets containing Lorem Ipsum passages, and more recently with desktop publishing software like PageCraft Studio including versions of Lorem Ipsum.</p>
    <p>Lorem Ipsum is simply dummy text of the printing and typesetting industry. Lorem Ipsum has been the industry's standard dummy text ever since the 1500s, when an unknown printer took a galley of type and scrambled it to make a type specimen book.</p>
    <p>It has survived not only five centuries, but also the leap into electronic typesetting, remaining essentially unchanged. It was popularised in the 1960s with the release of Marlowe Press sheets containing Lorem IpsumIpsum passages.</p>
  </div>

  <p class="block closing">Yours Sincerely</p>
  <div class="block signatory">
    <p class="signatory-name">Daniel Hartley</p>
    <p class="signatory-title">Managing Director</p>
  </div>

  <div class="footer-rule"></div>
  <footer class="footer-band">
    <p class="footer-address">448 Willowmere Ave, Ste 210, Folsom, CA 95999</p>
    <ul class="footer-contacts">
      <li>916-555-0187 <svg viewBox="0 0 12 12"><rect x="3" y="1" width="6" height="10" rx="1.5"/></svg></li>
      <li>info@brightfieldventures.example <svg viewBox="0 0 12 12"><rect x="1" y="2.5" width="10" height="7"/></svg></li>
      <li>brightfieldventures.example <svg viewBox="0 0 12 12"><circle cx="6" cy="6" r="5"/></svg></li>
    </ul>
  </footer>
</main>
</body>
</html>
```